professional business card design

Business card design. Photos have been uploaded and i am open to the designer choosing which photos to use. Would like the card to be mostyly in a grey scale design with black, whites, silver & grey colours. I have added copy of our flyer as would like on the back side of card our services to be listed. Do not use any bright colurs such as blue red green or yellow. i need to be able to edit the phone number and naem in the final card design submitted.

Target Market(s)

Clients

Industry/Entity Type

earhmovibng and transport

Contact Information for Business Card

Director Name, address, email, phone number and services

Colors

Designer to choose only greyscale colors for use in the design.

Requirements
Should not have
• no yellow, red, blue or green

```html
<!DOCTYPE html>
<html lang="en">
<head>
<meta charset="utf-8">
<title>RHS Business Card</title>
<link href="https://fonts.googleapis.com/css2?family=Arimo:wght@400;700&display=swap" rel="stylesheet">
<style>
  :root {
    --page: #d9d6d1;
    --card-black: #0c0c0c;
    --card-dark: #1c1c1c;
    --silver-light: #f4f4f4;
    --silver-mid: #c9c9c9;
    --silver-dark: #8d8d8d;
    --ink: #111111;
    --white: #ffffff;
    --grey-text: #4a4a4a;
  }
  * { margin: 0; padding: 0; box-sizing: border-box; }
  html, body { width: 900px; height: 1200px; overflow: hidden; }
  body { background: var(--page); font-family: "Arimo", Arial, sans-serif; position: relative; }

  .card {
    position: absolute; left: 78px; width: 744px; height: 442px;
    border-radius: 28px; overflow: hidden;
    background: radial-gradient(ellipse at 40% 30%, var(--card-dark), var(--card-black) 70%);
    box-shadow: 0 6px 14px rgba(0,0,0,.35);
  }
  .card--front { top: 130px; }
  .card--back { top: 638px; }

  .brand {
    position: absolute; left: 40px; top: 42px;
    font-weight: 700; font-size: 72px; letter-spacing: 10px; color: var(--silver-mid);
  }
  .truck-photo { position: absolute; left: 352px; top: 20px; }

  .name-band {
    position: absolute; left: 0; top: 225px; width: 392px; height: 53px;
    background: linear-gradient(90deg, var(--silver-light) 0%, var(--silver-mid) 70%, rgba(140,140,140,0) 100%);
    padding: 7px 0 0 26px;
  }
  .name { font-weight: 700; font-size: 26px; color: var(--ink); line-height: 1; }
  .role { font-weight: 700; font-size: 15px; color: var(--grey-text); margin-top: 3px; }

  .contacts { position: absolute; left: 26px; top: 302px; list-style: none; }
  .contacts li { display: flex; align-items: center; height: 24px; color: var(--white); font-size: 16.5px; font-weight: 700; letter-spacing: .3px; }
  .contacts svg { width: 16px; height: 16px; margin-right: 14px; fill: var(--white); }

  .depot-band {
    position: absolute; left: 0; top: 397px; width: 744px; height: 30px;
    background: linear-gradient(90deg, var(--silver-light), var(--silver-mid) 80%, var(--silver-dark));
    padding-left: 26px; font-weight: 700; font-size: 16.5px; line-height: 30px; color: var(--ink);
  }

  .haul-photo { position: absolute; left: 0; top: 0; }

  .services-band {
    position: absolute; left: 420px; top: 42px; width: 324px; height: 44px;
    background: linear-gradient(90deg, var(--silver-dark), var(--silver-light) 25%, var(--white));
    clip-path: polygon(24px 0, 100% 0, 100% 100%, 0 100%);
    text-align: right; padding-right: 30px;
    font-weight: 700; font-size: 24px; line-height: 44px; color: var(--ink);
  }
  .services { position: absolute; right: 24px; top: 104px; list-style: none; text-align: right; }
  .services li {
    color: var(--white); font-size: 15px; height: 29.2px; line-height: 29.2px;
    display: flex; justify-content: flex-end; align-items: center;
  }
  .services li::after { content: ""; width: 11px; height: 11px; background: var(--white); margin-left: 10px; }
</style>
</head>
<body>

<section class="card card--front">
  <div class="brand">RHS</div>

  <svg class="truck-photo" width="392" height="345" role="img" aria-label="Photo of a white prime mover truck with an oversize sign">
    <defs>
      <linearGradient id="truckTone" x1="0" y1="0" x2="1" y2="1">
        <stop offset="0" stop-color="#e9ecef"/>
        <stop offset="0.6" stop-color="#a9adb1"/>
        <stop offset="1" stop-color="#3a3a3a"/>
      </linearGradient>
    </defs>
    <rect width="392" height="345" rx="10" fill="url(#truckTone)"/>
  </svg>

  <div class="name-band">
    <div class="name">DANIEL HART</div>
    <div class="role">Director</div>
  </div>

  <ul class="contacts">
    <li><svg viewBox="0 0 16 16"><path d="M1 6c0-2 3-3 7-3s7 1 7 3v1h-4V5.5H5V7H1zM3 8h10l1 6H2z"/></svg>000 444 000</li>
    <li><svg viewBox="0 0 16 16"><path d="M1 3h14v10H1zM2 4l6 5 6-5v1l-6 5-6-5z" fill-rule="evenodd"/></svg>info@ridgelinehaulage.com.au</li>
    <li><svg viewBox="0 0 16 16"><circle cx="8" cy="8" r="6.5" fill="none" stroke="#fff" stroke-width="2"/><path d="M5 5l3 1 1 3-2 3-1-3z"/></svg>www.websiteaddress.com.au</li>
  </ul>

  <div class="depot-band">DEPOT :RHS LOT 114, NINE MILE ROAD, DUSTY CREEK, AUSTRALIA</div>
</section>

<section class="card card--back">
  <svg class="haul-photo" width="744" height="442" role="img" aria-label="Photo of a truck hauling a grader on a low loader under blue sky">
    <defs>
      <linearGradient id="haulTone" x1="0" y1="0" x2="0" y2="1">
        <stop offset="0" stop-color="#8fb3d6"/>
        <stop offset="0.45" stop-color="#dfe6ec"/>
        <stop offset="0.7" stop-color="#9a9d9f"/>
        <stop offset="1" stop-color="#4b4c4d"/>
      </linearGradient>
    </defs>
    <polygon points="0,0 482,0 297,442 0,442" fill="url(#haulTone)"/>
  </svg>

  <div class="services-band">OUR SER VICES</div>

  <ul class="services">
    <li>Over size load / Hot Shot Load</li>
    <li>Heavy Vehicle Recovery services</li>
    <li>potable water delivers</li>
    <li>Road Building / Maintenance</li>
    <li>Earthworks</li>
    <li>Send &amp; Metal Supply &amp; cartage</li>
    <li>Road train Trippers</li>
    <li>Road train Tankers</li>
    <li>Road train flat tops</li>
    <li>Drop Deck Trailers</li>
    <li>Mine site accredited equipment &amp; oparetors</li>
  </ul>
</section>

</body>
</html>
```